MRT Property - Business Cards

Looking for a business card & general letterhead, signage etc design for our new logo.

Colours:
000a20
0056a2
00b5ef
0088ce
68cef2

Fonts:
Poppins
Karla

Please keep look and feel of new brand - example in the zip package I sent.

```html
<!DOCTYPE html>
<html lang="en">
<head>
<meta charset="utf-8">
<title>MRT Property – Stationery</title>
<link rel="stylesheet" href="https://fonts.googleapis.com/css2?family=Poppins:wght@400;600&display=swap">
<style>
  :root {
    --ink: #000a20;
    --navy: #0056a2;
    --cyan: #00b5ef;
    --mid: #0088ce;
    --sky: #68cef2;
    --paper: #ffffff;
    --card-paper: #f1f1f2;
    --envelope: #0c4f98;
    --envelope-flap: #0a4a8f;
    --backdrop: #e2e2e3;
  }
  * { margin: 0; padding: 0; box-sizing: border-box; }
  html, body { width: 1200px; height: 686px; overflow: hidden; }
  body {
    background: var(--backdrop);
    font-family: "Poppins", sans-serif;
    color: var(--ink);
    position: relative;
  }

  /* Letterhead */
  .letterhead {
    position: absolute; left: 70px; top: 30px;
    width: 440px; height: 626px;
    background: var(--paper);
    box-shadow: 0 4px 14px rgba(0,0,0,.18);
    overflow: hidden;
  }
  .rule { position: absolute; left: 0; right: 0; height: 1px; background: var(--sky); }
  .rule .accent { position: absolute; top: -1px; height: 3px; background: var(--mid); }
  .letterhead .rule--top { top: 92px; }
  .letterhead .rule--top .accent { left: 62%; width: 30%; }
  .letterhead .brand {
    position: absolute; right: 34px; top: 48px;
    font-weight: 600; font-size: 24px; color: var(--mid);
    letter-spacing: .5px;
  }
  .letterhead .rule--foot { top: 530px; }
  .letterhead .rule--foot .accent { left: 24%; width: 36%; }
  .letterhead .contact {
    position: absolute; left: 26px; right: 26px; top: 540px;
    display: grid; grid-template-columns: auto 1fr; gap: 4px 14px;
    font-size: 9px; line-height: 1.5;
  }
  .band { position: absolute; left: 0; bottom: 0; width: 100%; height: 26px; }

  .contact-item { display: flex; align-items: center; gap: 5px; white-space: nowrap; }
  .contact-item svg { width: 9px; height: 9px; flex: none; }
  .letterhead .contact-item--address { white-space: normal; align-items: flex-start; }
  .letterhead .contact-item--address svg { margin-top: 3px; }

  /* Compliment slip */
  .slip {
    position: absolute; left: 610px; top: 60px;
    width: 540px; height: 270px;
    background: var(--card-paper);
    box-shadow: 0 4px 14px rgba(0,0,0,.18);
    overflow: hidden;
  }
  .slip .brand {
    position: absolute; right: 40px; top: 104px;
    font-weight: 600; font-size: 26px; color: var(--navy);
  }
  .slip .rule--foot { top: 196px; }
  .slip .rule--foot .accent { left: 28%; width: 32%; }
  .slip .contact {
    position: absolute; left: 26px; right: 26px; top: 206px;
    display: grid; grid-template-columns: auto 1fr; gap: 3px 40px;
    font-size: 8.5px; line-height: 1.45;
  }
  .slip .band { height: 18px; }

  /* Envelope */
  .envelope {
    position: absolute; left: 610px; top: 370px;
    width: 540px; height: 270px;
    background: var(--envelope);
    box-shadow: 0 6px 16px rgba(0,0,0,.25);
    overflow: hidden;
  }
  .envelope svg.flap { position: absolute; inset: 0; }
  .envelope .brand {
    position: absolute; left: 0; right: 0; top: 78px; text-align: center;
    font-weight: 600; font-size: 16px; color: var(--sky);
  }
</style>
</head>
<body>

  <section class="letterhead" aria-label="Letterhead">
    <div class="rule rule--top"><span class="accent"></span></div>
    <div class="brand">MRT Property</div>

    <div class="rule rule--foot"><span class="accent"></span></div>
    <div class="contact">
      <span class="contact-item">
        <svg viewBox="0 0 10 10"><path d="M2 1h2l1 2.5-1.3.8a6 6 0 0 0 2 2l.8-1.3L9 6v2a1 1 0 0 1-1 1A7 7 0 0 1 1 2a1 1 0 0 1 1-1z" fill="var(--mid)"/></svg>
        +61 2 5550 1234
      </span>
      <span class="contact-item contact-item--address">
        <svg viewBox="0 0 10 10"><path d="M5 0.5a3.3 3.3 0 0 0-3.3 3.3C1.7 6.3 5 9.5 5 9.5s3.3-3.2 3.3-5.7A3.3 3.3 0 0 0 5 .5zm0 4.6a1.3 1.3 0 1 1 0-2.6 1.3 1.3 0 0 1 0 2.6z" fill="var(--mid)"/></svg>
        <span>Suite 4.12, Level 4, 18 Harbour Lane, Riverside Park NSW 2140</span>
      </span>
      <span class="contact-item">
        <svg viewBox="0 0 10 10"><rect x="0.5" y="2" width="9" height="6" rx="1" fill="var(--mid)"/><path d="M1 2.5l4 3 4-3" stroke="#fff" stroke-width=".8" fill="none"/></svg>
        info@mrtproperty.com.au
      </span>
      <span class="contact-item">
        <svg viewBox="0 0 10 10"><circle cx="5" cy="5" r="4.3" fill="var(--mid)"/><path d="M.8 5h8.4M5 .7c-2.2 2.5-2.2 6.1 0 8.6M5 .7c2.2 2.5 2.2 6.1 0 8.6" stroke="#fff" stroke-width=".6" fill="none"/></svg>
        www.mrtproperty.com.au
      </span>
    </div>

    <svg class="band" viewBox="0 0 440 26" preserveAspectRatio="none" aria-hidden="true">
      <rect width="440" height="26" fill="var(--sky)"/>
      <polygon points="0,0 180,0 200,26 0,26" fill="var(--mid)"/>
      <polygon points="180,0 196,0 216,26 200,26" fill="var(--paper)"/>
    </svg>
  </section>

  <section class="slip" aria-label="Compliment slip">
    <div class="brand">MRT Property</div>

    <div class="rule rule--foot"><span class="accent"></span></div>
    <div class="contact">
      <span class="contact-item">
        <svg viewBox="0 0 10 10"><path d="M2 1h2l1 2.5-1.3.8a6 6 0 0 0 2 2l.8-1.3L9 6v2a1 1 0 0 1-1 1A7 7 0 0 1 1 2a1 1 0 0 1 1-1z" fill="var(--mid)"/></svg>
        +61 2 5550 1234
      </span>
      <span class="contact-item">
        <svg viewBox="0 0 10 10"><path d="M5 0.5a3.3 3.3 0 0 0-3.3 3.3C1.7 6.3 5 9.5 5 9.5s3.3-3.2 3.3-5.7A3.3 3.3 0 0 0 5 .5zm0 4.6a1.3 1.3 0 1 1 0-2.6 1.3 1.3 0 0 1 0 2.6z" fill="var(--mid)"/></svg>
        Suite 4.12, Level 4, 18 Harbour Lane, Riverside Park NSW 2140
      </span>
      <span class="contact-item">
        <svg viewBox="0 0 10 10"><rect x="0.5" y="2" width="9" height="6" rx="1" fill="var(--mid)"/><path d="M1 2.5l4 3 4-3" stroke="#fff" stroke-width=".8" fill="none"/></svg>
        info@mrtproperty.com.au
      </span>
      <span class="contact-item">
        <svg viewBox="0 0 10 10"><circle cx="5" cy="5" r="4.3" fill="var(--mid)"/><path d="M.8 5h8.4M5 .7c-2.2 2.5-2.2 6.1 0 8.6M5 .7c2.2 2.5 2.2 6.1 0 8.6" stroke="#fff" stroke-width=".6" fill="none"/></svg>
        www.mrtproperty.com.au
      </span>
    </div>

    <svg class="band" viewBox="0 0 540 18" preserveAspectRatio="none" aria-hidden="true">
      <rect width="540" height="18" fill="var(--sky)"/>
      <polygon points="0,0 200,0 214,18 0,18" fill="var(--mid)"/>
      <polygon points="200,0 212,0 226,18 214,18" fill="var(--card-paper)"/>
    </svg>
  </section>

  <section class="envelope" aria-label="Envelope">
    <svg class="flap" viewBox="0 0 540 270" preserveAspectRatio="none" aria-hidden="true">
      <path d="M0,0 H540 L290,150 Q270,162 250,150 Z" fill="var(--envelope-flap)"/>
      <path d="M0,0 L250,150 Q270,162 290,150 L540,0" stroke="rgba(0,0,0,.18)" stroke-width="2" fill="none"/>
    </svg>
    <div class="brand">MRT Property</div>
  </section>

</body>
</html>
```